Wordpress Design Project for Employee Communications Site

We need a Wordpress design for a company that strategizes on and produces materials for employee communications. Improving employee communications at all levels of an organization can help improve overall company performance and results. The site needs to look very clean and professional; we're not afraid of white space. We like the functionality that Wordpress provides; however, we only want one "true" blog page; the other pages should give the impression of a more "static" web site - particularly the home page. I have a logo that I can provide.

I have added these comments to the discussion page:
Great question - thank you for asking it. I’ve done more research

I like the very clean and monochromatic looks to many of these. I don’t have to have monochromatic, but I do like minimal colors. Simple, clean, organized. The home page should “fit” almost entirely without scrolling. I do like fat footers that you can scroll down to. I don’t want a colored background, but any that I’ve chosen with colored backgrounds could be switched to a white background.

http://www.mirabelquennet.example/
http://pondraft.example/
http://v1.samplumworth.example/
http://howdythegoat.example/
http://stayingbrisk.example/
http://www.interiors.kelmun.example/
http://trelvmasters.example/

These last two are more corporate sites. The first one is from a well-respected consultant in my area who does a lot of what I do. And I think Harwenby does a nice job with their site. So, I want to marry the look I like with getting the content job done.

http://www.messagefuelbox.example/
http://www.harwenby.example/view/en_US/us/index.htm

Target Market(s)

Target market is mid- to large-sized companies. More than 500 employees.

Industry/Entity Type

Communications

Requirements
Must have
• Need an impactful home page. There should be a "blog" page; contact us; services; about. For starters, at least. I want fonts to be very readable - that is, either quite dark gray or black.
Nice to have
• I am loathe to include a picture of myself, but I do want some images that say, "professional" and "expert" in communications.
Should not have
• I don't want a hits counter :) (I know no one would do that!).

```html
<!DOCTYPE html>
<html lang="en">
<head>
<meta charset="utf-8">
<title>Northvale Staff Messaging Group</title>
<link rel="stylesheet" href="https://fonts.googleapis.com/css2?family=Yanone+Kaffeesatz:wght@300;400&family=PT+Sans+Narrow:wght@400&display=swap">
<style>
  :root {
    --ink: #333333;
    --ink-soft: #555555;
    --lime: #bcd634;
    --lime-deep: #a8c21f;
    --charcoal: #444444;
    --night: #2e2e2e;
    --rule: #b5b5b5;
    --card-line: #cfcfcf;
    --muted: #8a8a8a;
    --paper: #ffffff;
    --photo-a: #c9c4bd;
    --photo-b: #6d6a68;
  }
  * { margin: 0; padding: 0; box-sizing: border-box; }
  html, body { width: 1200px; height: 1000px; overflow: hidden; background: var(--paper); }
  body { position: relative; font-family: "PT Sans Narrow", "Arial Narrow", sans-serif; color: var(--ink); }

  .top-bar { position: absolute; left: 0; top: 0; width: 1200px; height: 5px; background: var(--night); }

  .brand { position: absolute; left: 0; top: 42px; width: 1200px; display: flex; justify-content: center; align-items: center; gap: 14px; }
  .brand-dot { width: 34px; height: 34px; border-radius: 50%; background: var(--lime); }
  .brand-name { font-family: "Yanone Kaffeesatz", sans-serif; font-weight: 300; font-size: 52px; color: var(--lime-deep); letter-spacing: 1px; line-height: 1; }

  .dash-rule { position: absolute; height: 0; border-top: 2px dashed var(--rule); }
  .dash-rule.header { left: 105px; top: 139px; width: 990px; }
  .dash-rule.footer { left: 108px; top: 947px; width: 990px; }

  .main-nav { position: absolute; top: 145px; left: 0; width: 1200px; height: 32px; }
  .main-nav a { position: absolute; top: 0; font-family: "Yanone Kaffeesatz", sans-serif; font-size: 23px; letter-spacing: 1.2px; color: var(--ink); text-decoration: none; line-height: 32px; }
  .main-nav a.is-current { color: var(--lime); }
  .nav-sep { position: absolute; top: 0; width: 1px; height: 32px; background: #d8d8d8; }
  .nav-marker { position: absolute; left: 299px; top: 140px; width: 0; height: 0; border-left: 7px solid transparent; border-right: 7px solid transparent; border-top: 6px solid var(--night); }

  .hero { position: absolute; left: 100px; top: 185px; width: 1000px; height: 348px; background: var(--lime); }
  .hero-shadow { position: absolute; left: 40px; top: 520px; width: 1120px; height: 40px; border-radius: 50%; background: radial-gradient(ellipse at center, rgba(0,0,0,0.22) 0%, rgba(0,0,0,0) 70%); }
  .hero-edge { position: absolute; left: 0; top: 0; width: 12px; height: 348px; background: var(--night); }
  .hero-photo { position: absolute; left: 23px; top: 0; width: 522px; height: 348px; background: linear-gradient(135deg, var(--photo-a) 0%, #9e9893 50%, var(--photo-b) 100%); }
  .hero-banner { position: absolute; left: 482px; top: 12px; width: 516px; height: 120px; }
  .hero-title { position: absolute; left: 607px; top: 40px; font-family: "Yanone Kaffeesatz", sans-serif; font-weight: 400; font-size: 46px; color: var(--ink); line-height: 60px; white-space: nowrap; }
  .hero-copy { position: absolute; left: 600px; top: 152px; width: 370px; font-family: "Yanone Kaffeesatz", sans-serif; font-weight: 300; font-size: 21.5px; line-height: 25px; text-align: justify; color: var(--ink); }
  .slider-dots { position: absolute; left: 730px; top: 288px; display: flex; align-items: center; gap: 9px; font-family: "Yanone Kaffeesatz", sans-serif; font-size: 30px; color: #8d9a52; }
  .slider-dot { width: 16px; height: 16px; border-radius: 50%; border: 1px solid #666; background: radial-gradient(circle at 40% 35%, #ffffff, #cfcfcf); }
  .slider-dot.is-active { background: radial-gradient(circle at 40% 35%, #888, #444); }

  .feature-card { position: absolute; top: 590px; height: 299px; border: 1px solid var(--card-line); background: var(--paper); }
  .feature-head { height: 50px; background: var(--charcoal); display: flex; align-items: center; padding-left: 8px; gap: 8px; }
  .feature-head h2 { font-family: "Yanone Kaffeesatz", sans-serif; font-weight: 400; font-size: 23px; color: #ffffff; letter-spacing: 0.3px; }
  .feature-photo { height: 113px; background: linear-gradient(135deg, #d5d2ce 0%, #8f8b88 55%, #4f4d4d 100%); }
  .feature-copy { padding: 8px 7px 0 7px; font-size: 14.6px; line-height: 18px; text-align: justify; color: var(--ink); }
  .read-more { position: absolute; left: 0; bottom: 6px; width: 100%; text-align: center; font-family: "Yanone Kaffeesatz", sans-serif; font-weight: 300; font-size: 16px; color: var(--muted); word-spacing: 10px; }

  .site-footer { position: absolute; left: 0; top: 953px; width: 1200px; height: 47px; background: var(--charcoal); font-family: Arial, Helvetica, sans-serif; font-size: 13px; color: #ffffff; }
  .footer-nav { position: absolute; left: 105px; top: 19px; display: flex; gap: 22px; }
  .footer-nav a { color: #ffffff; text-decoration: none; display: flex; align-items: center; gap: 4px; }
  .footer-nav svg, .feature-head svg { display: block; }
  .footer-legal { position: absolute; right: 99px; top: 19px; }
</style>
</head>
<body>
  <div class="top-bar"></div>

  <header>
    <div class="brand">
      <span class="brand-dot"></span>
      <span class="brand-name">Northvale Staff Messaging Group</span>
    </div>
    <div class="dash-rule header"></div>
    <span class="nav-marker"></span>
    <nav class="main-nav">
      <a class="is-current" href="#" style="left:287px">HOME</a>
      <span class="nav-sep" style="left:370px"></span>
      <a href="#" style="left:412px">ABOUT</a>
      <span class="nav-sep" style="left:498px"></span>
      <a href="#" style="left:546px">SERVICES</a>
      <span class="nav-sep" style="left:648px"></span>
      <a href="#" style="left:696px">BLOG</a>
      <span class="nav-sep" style="left:773px"></span>
      <a href="#" style="left:816px">CONTACT US</a>
    </nav>
  </header>

  <div class="hero-shadow"></div>
  <section class="hero">
    <div class="hero-edge"></div>
    <div class="hero-photo" role="img" aria-label="Photo of a business team discussing documents around a meeting table"></div>
    <svg class="hero-banner" viewBox="0 0 516 120" aria-hidden="true">
      <defs>
        <linearGradient id="bannerFill" x1="0" y1="0" x2="0" y2="1">
          <stop offset="0" stop-color="#fbfbfb"/>
          <stop offset="1" stop-color="#c9c9c9"/>
        </linearGradient>
      </defs>
      <polygon points="0,60 58,0 516,0 516,120 58,120" fill="url(#bannerFill)"/>
    </svg>
    <h1 class="hero-title">Effective Communication</h1>
    <p class="hero-copy">Effective communication in the workplace is the backbone of any business. Without it, you could miss out on important opportunities, waste time and cause your employees and customers to become frustrated.</p>
    <div class="slider-dots">
      <span>{</span>
      <span class="slider-dot is-active"></span>
      <span class="slider-dot"></span>
      <span class="slider-dot"></span>
      <span class="slider-dot"></span>
      <span>}</span>
    </div>
  </section>

  <main>
    <article class="feature-card" style="left:99px;width:247px">
      <div class="feature-head">
        <svg width="24" height="14" viewBox="0 0 24 14" aria-hidden="true"><path d="M1 1l6 6-6 6M11 1l6 6-6 6" fill="none" stroke="#bcd634" stroke-width="3"/></svg>
        <h2>COMMUNICATION PROCESS</h2>
      </div>
      <div class="feature-photo" role="img" aria-label="Photo of a seated audience listening to a presenter"></div>
      <p class="feature-copy">Effective communication in the workplace is the backbone of any business. Without it, you could miss out on important opportunities, waste time and cause your employees and customers to become frustrated.</p>
      <div class="read-more">{ Read More }</div>
    </article>
    <article class="feature-card" style="left:350px;width:250px">
      <div class="feature-head">
        <svg width="24" height="14" viewBox="0 0 24 14" aria-hidden="true"><path d="M1 1l6 6-6 6M11 1l6 6-6 6" fill="none" stroke="#bcd634" stroke-width="3"/></svg>
        <h2>Communication Process</h2>
      </div>
      <div class="feature-photo" role="img" aria-label="Photo of a cheering team raising their hands in a workshop"></div>
      <p class="feature-copy">Effective communication in the workplace is the backbone of any business. Without it, you could miss out on important opportunities, waste time and cause your employees and customers to become frustrated.</p>
      <div class="read-more">{ Read More }</div>
    </article>
    <article class="feature-card" style="left:603px;width:247px">
      <div class="feature-head">
        <svg width="24" height="14" viewBox="0 0 24 14" aria-hidden="true"><path d="M1 1l6 6-6 6M11 1l6 6-6 6" fill="none" stroke="#bcd634" stroke-width="3"/></svg>
        <h2>Communication Process</h2>
      </div>
      <div class="feature-photo" role="img" aria-label="Photo of two colleagues reviewing work together at a desk"></div>
      <p class="feature-copy">Effective communication in the workplace is the backbone of any business. Without it, you could miss out on important opportunities, waste time and cause your employees and customers to become frustrated.</p>
      <div class="read-more">{ Read More }</div>
    </article>
    <article class="feature-card" style="left:853px;width:248px">
      <div class="feature-head">
        <svg width="24" height="14" viewBox="0 0 24 14" aria-hidden="true"><path d="M1 1l6 6-6 6M11 1l6 6-6 6" fill="none" stroke="#bcd634" stroke-width="3"/></svg>
        <h2>Communication Process</h2>
      </div>
      <div class="feature-photo" role="img" aria-label="Photo of a business team in discussion around a meeting table"></div>
      <p class="feature-copy">Effective communication in the workplace is the backbone of any business. Without it, you could miss out on important opportunities, waste time and cause your employees and customers to become frustrated.</p>
      <div class="read-more">{ Read More }</div>
    </article>
  </main>

  <div class="dash-rule footer"></div>
  <footer class="site-footer">
    <nav class="footer-nav">
      <a href="#"><svg width="8" height="10" viewBox="0 0 8 10" aria-hidden="true"><path d="M1 1l4 4-4 4" fill="none" stroke="#bcd634" stroke-width="2.4"/></svg>Home</a>
      <a href="#"><svg width="8" height="10" viewBox="0 0 8 10" aria-hidden="true"><path d="M1 1l4 4-4 4" fill="none" stroke="#bcd634" stroke-width="2.4"/></svg>About</a>
      <a href="#"><svg width="8" height="10" viewBox="0 0 8 10" aria-hidden="true"><path d="M1 1l4 4-4 4" fill="none" stroke="#bcd634" stroke-width="2.4"/></svg>Services</a>
      <a href="#"><svg width="8" height="10" viewBox="0 0 8 10" aria-hidden="true"><path d="M1 1l4 4-4 4" fill="none" stroke="#bcd634" stroke-width="2.4"/></svg>Blog</a>
      <a href="#"><svg width="8" height="10" viewBox="0 0 8 10" aria-hidden="true"><path d="M1 1l4 4-4 4" fill="none" stroke="#bcd634" stroke-width="2.4"/></svg>Contact Us</a>
    </nav>
    <p class="footer-legal">All rights reserved. © Northvale Staff Messaging Group 2008</p>
  </footer>
</body>
</html>
```